New Business Card Design for Manufacturing

We are an engineering/manufacturing company that offers Advanced machining/assembly/engineering services, as well as innovative products for the heavy duty engine cooling markets.

We are looking to get a new business card designed that is clean and modern looking, but still fits the wide range of technical/skilled work we do.

- We hope to use this design as the base for other design work in new Presentations, web, and print work.

Industry/Entity Type

Engineering

Contact Information for Business Card

Our preferred color of blue is (RGB) 22/71/159 but can vary slightly from that color. Our content will be our Logo and full company name (Vantrell Forge Works, Inc.), company address, name, job title, phone number with extension, cell number, fax number, website, and email address on the cards.
We'd like the full company name next to the logo, but we are open to other interpretations of that layout.
Preferably, we would like the back side to be clean with just our logo, and the front to contain all of the contact information.

Colors
2f74b4
0355a3
85abd2

Requirements
Must have
• - Logo, company name, needed content - We are open to interpretation beyond that.
• - Standard size business card.
• - Horizontal orientation.
• - Enough space for lengthy names / job titles (for example, a job title could read "Directory of Human Resources" or "V.P. of Governmental Affairs"). We need this to look clean, whether the title be short (CEO) or long (as described above).

```html
<!DOCTYPE html>
<html lang="en">
<head>
<meta charset="utf-8">
<title>Vantrell Forge Works – Business Card</title>
<link rel="stylesheet" href="https://fonts.googleapis.com/css2?family=Archivo:wght@800&family=Lato:wght@300;400;700&display=swap">
<style>
  :root {
    --navy: #1b2a78;
    --brand-blue: #16479f;
    --steel: #6f86ad;
    --card-white: #f4f5f8;
    --ink-grey: #7a8090;
    --contact-ink: #c9cfe2;
    --page-bg: #e7e4df;
  }
  * { margin: 0; padding: 0; box-sizing: border-box; }
  html, body {
    width: 1200px; height: 970px; overflow: hidden;
    background: var(--page-bg);
  }
  .card {
    position: absolute; left: 80px; top: 188px;
    width: 1040px; height: 595px;
    background: linear-gradient(160deg, #ffffff 0%, var(--card-white) 60%, #e9ecf2 100%);
    overflow: hidden;
    box-shadow: 0 18px 40px rgba(40, 40, 60, 0.22);
  }
  .card-swoosh { position: absolute; inset: 0; width: 100%; height: 100%; }
  .brand {
    position: absolute; left: 56px; top: 78px;
  }
  .brand-name {
    font-family: "Archivo", sans-serif; font-weight: 800;
    font-size: 50px; line-height: 1; letter-spacing: 0.5px;
    color: var(--navy); text-transform: uppercase;
  }
  .brand-tagline {
    margin-top: 26px;
    font-family: "Archivo", sans-serif; font-weight: 800;
    font-size: 23px; letter-spacing: 0.5px;
    color: var(--navy); text-transform: uppercase;
  }
  .person { position: absolute; left: 55px; top: 288px; }
  .person-name {
    font-family: "Lato", sans-serif; font-weight: 700;
    font-size: 31px; color: var(--navy); text-transform: uppercase;
  }
  .person-title {
    font-family: "Lato", sans-serif; font-weight: 400;
    font-size: 24px; color: var(--ink-grey); line-height: 1;
  }
  .contact {
    position: absolute; right: 44px; top: 380px;
    list-style: none;
    font-family: "Lato", sans-serif; font-weight: 300;
    font-size: 24px; color: var(--contact-ink);
  }
  .contact li {
    display: flex; justify-content: flex-end; align-items: center;
    gap: 12px; height: 34.5px;
  }
  .contact svg { width: 28px; height: 28px; flex: none; }
</style>
</head>
<body>
  <main class="card">
    <svg class="card-swoosh" viewBox="0 0 1040 595" preserveAspectRatio="none" aria-hidden="true">
      <defs>
        <linearGradient id="navy-fill" x1="0" y1="1" x2="1" y2="0">
          <stop offset="0" stop-color="#1e2d80"/>
          <stop offset="0.6" stop-color="#213a92"/>
          <stop offset="1" stop-color="#1a2a78"/>
        </linearGradient>
        <linearGradient id="steel-fill" x1="0" y1="0" x2="1" y2="0">
          <stop offset="0" stop-color="#7d92b6"/>
          <stop offset="1" stop-color="#3c5595"/>
        </linearGradient>
      </defs>
      <path d="M0 435 C 330 420, 640 360, 840 230 L 840 595 L 0 595 Z" fill="url(#steel-fill)"/>
      <path d="M0 535 C 420 500, 820 340, 1040 0 L 1040 595 L 0 595 Z" fill="url(#navy-fill)"/>
      <path d="M0 535 C 420 500, 820 340, 1040 0" fill="none" stroke="#c9b9c4" stroke-width="2.5"/>
    </svg>

    <header class="brand">
      <p class="brand-name">Vantrell Forge Works, Inc.</p>
      <p class="brand-tagline">Built for the Long Haul</p>
    </header>

    <section class="person">
      <h1 class="person-name">Dana Whitlock</h1>
      <p class="person-title">Founder</p>
    </section>

    <ul class="contact">
      <li>(555) 014-2290
        <svg viewBox="0 0 28 28" fill="none" stroke="currentColor" stroke-width="1.5"><circle cx="14" cy="14" r="12.5"/><rect x="10" y="7" width="8" height="14" rx="1.5"/><line x1="13" y1="18.5" x2="15" y2="18.5"/></svg>
      </li>
      <li>(555) 014-2291
        <svg viewBox="0 0 28 28" fill="none" stroke="currentColor" stroke-width="1.5"><circle cx="14" cy="14" r="12.5"/><rect x="10" y="7.5" width="8" height="4"/><rect x="7.5" y="11.5" width="13" height="6" fill="currentColor"/><rect x="10" y="17.5" width="8" height="3.5"/></svg>
      </li>
      <li>info@vantrellforge.com
        <svg viewBox="0 0 28 28" fill="none" stroke="currentColor" stroke-width="1.5"><circle cx="14" cy="14" r="12.5"/><rect x="7.5" y="9.5" width="13" height="9" fill="currentColor"/><path d="M7.5 9.5 L14 15 L20.5 9.5" stroke="#1e2d80"/></svg>
      </li>
      <li>www.vantrellforge.com
        <svg viewBox="0 0 28 28" fill="none" stroke="currentColor" stroke-width="1.5"><circle cx="14" cy="14" r="12.5"/><circle cx="14" cy="14" r="7"/><ellipse cx="14" cy="14" rx="3" ry="7"/><line x1="7" y1="14" x2="21" y2="14"/></svg>
      </li>
      <li>PO Box 418, 27 Kestrel Street, Melbourne
        <svg viewBox="0 0 28 28" fill="none" stroke="currentColor" stroke-width="1.5"><circle cx="14" cy="14" r="12.5"/><path d="M14 21 C 10 16, 9 14, 9 12 A5 5 0 0 1 19 12 C 19 14, 18 16, 14 21 Z"/><circle cx="14" cy="12" r="1.8"/></svg>
      </li>
    </ul>
  </main>
</body>
</html>
```